QVR business card

Need a business card for a company that provides instructional design and elearning development services. The website is here: http://quorvane.studio/

I'm attaching a current logo, as well as the old business card design. While I like to keep it clean, the old design is too simplistic for my liking. The only idea I want to reuse from the old design is placing industry jargon on the back of the card, just need a better way to present it. But if you have other ideas for the back--feel free to experiment.

Please use the colors complementary to the color we have on the website. Thank you!

```html
<!DOCTYPE html>
<html lang="en">
<head>
<meta charset="utf-8">
<title>QVR business card</title>
<link rel="stylesheet" href="https://fonts.googleapis.com/css2?family=Montserrat:wght@700&family=Roboto+Condensed:wght@700&family=Ubuntu:wght@400;500&family=Roboto:wght@400&display=swap">
<style>
  :root {
    --backdrop: #a8a6a6;
    --card: #2f2f31;
    --teal: #1fb5a0;
    --sand: #d8d27f;
    --white: #ffffff;
    --ink-light: #c4c4c6;
    --ink-muted: #a9a9ac;
    --rule: #6a6a6d;
  }
  * { margin: 0; padding: 0; box-sizing: border-box; }
  html, body {
    width: 1200px; height: 1200px; overflow: hidden;
    background: var(--backdrop);
  }
  .stage { position: relative; width: 1200px; height: 1200px; }
  .card {
    position: absolute; width: 714px; height: 418px;
    background: var(--card); border-radius: 22px; overflow: hidden;
  }
  .card--services { left: 238px; top: 117px; }
  .card--contact { left: 231px; top: 644px; }
  .card svg { position: absolute; inset: 0; display: block; }

  .service-line {
    font-family: "Montserrat", sans-serif; font-weight: 700;
    font-size: 36px; fill: var(--teal);
  }
  .service-line--muted { fill: var(--sand); }
  .headline {
    font-family: "Roboto Condensed", sans-serif; font-weight: 700;
    font-size: 60px; fill: var(--white);
  }

  .wordmark {
    position: absolute; left: 0; width: 363px; top: 170px;
    text-align: center;
    font-family: "Ubuntu", sans-serif; font-weight: 500;
    font-size: 72px; line-height: 1; color: var(--teal);
    letter-spacing: 2px;
  }
  .divider {
    position: absolute; left: 363px; top: 49px; width: 1px; height: 300px;
    background: var(--rule);
  }
  .contact { position: absolute; left: 397px; top: 114px; }
  .contact__name {
    font-family: "Ubuntu", sans-serif; font-weight: 500;
    font-size: 20px; color: var(--ink-light); letter-spacing: 0.3px;
  }
  .contact__role {
    font-family: "Ubuntu", sans-serif; font-weight: 400;
    font-size: 15.5px; color: var(--ink-muted); margin-top: 6px;
  }
  .contact__list { list-style: none; margin-top: 40px; }
  .contact__item {
    display: flex; align-items: center; gap: 16px; height: 27px;
    font-family: "Roboto", sans-serif; font-size: 17px; color: var(--ink-light);
  }
  .contact__item svg { position: static; flex: none; }
  .email {
    position: absolute; left: 380px; top: 378px;
    font-family: "Roboto", sans-serif; font-size: 17px; color: var(--white);
  }
</style>
</head>
<body>
<main class="stage">

  <section class="card card--services" aria-label="Card back: services">
    <svg width="714" height="418" viewBox="0 0 714 418">
      <text class="service-line" x="42" y="64" textLength="630" lengthAdjust="spacingAndGlyphs">COURSE AUTHORING · VIDEO</text>
      <text class="service-line service-line--muted" x="42" y="116" textLength="630" lengthAdjust="spacingAndGlyphs">LEARNER ANALYTICS · UX</text>
      <text class="service-line" x="42" y="168" textLength="630" lengthAdjust="spacingAndGlyphs">MICROLEARNING · SIMULATION</text>
      <line x1="42" y1="186" x2="672" y2="186" stroke="var(--rule)" stroke-width="2"/>
      <text class="headline" x="42" y="246" textLength="630" lengthAdjust="spacingAndGlyphs">WHAT SHALL WE BUILD?</text>
      <line x1="42" y1="264" x2="672" y2="264" stroke="var(--rule)" stroke-width="2"/>
      <text class="service-line" x="42" y="306" textLength="630" lengthAdjust="spacingAndGlyphs">ONBOARDING · ASSESSMENTS</text>
      <text class="service-line service-line--muted" x="42" y="358" textLength="630" lengthAdjust="spacingAndGlyphs">STORYBOARDS · ACCESSIBILITY</text>
      <text class="service-line" x="42" y="396" textLength="630" lengthAdjust="spacingAndGlyphs" font-size="30">VIRTUAL TRAINING · CMI5</text>
    </svg>
  </section>

  <section class="card card--contact" aria-label="Card front: contact">
    <svg width="714" height="418" viewBox="0 0 714 418" aria-hidden="true">
      <polygon points="0,388 330,388 316,418 0,418" fill="var(--sand)"/>
      <polygon points="314,418 344,363 714,363 714,418" fill="var(--teal)"/>
    </svg>

    <div class="wordmark">QVR</div>
    <div class="divider"></div>

    <div class="contact">
      <p class="contact__name">Adrian Velkov</p>
      <p class="contact__role">Managing Director</p>
      <ul class="contact__list">
        <li class="contact__item">
          <svg width="18" height="14" viewBox="0 0 18 14" aria-hidden="true">
            <path d="M1 4 Q9 -1 17 4 L15 6 L12 5 L12 3 Q9 2 6 3 L6 5 L3 6 Z" fill="var(--teal)"/>
            <rect x="4" y="7" width="10" height="6" rx="1" fill="var(--teal)"/>
          </svg>
          <span>646-555-0182</span>
        </li>
        <li class="contact__item">
          <svg width="18" height="16" viewBox="0 0 16 16" aria-hidden="true">
            <circle cx="8" cy="8" r="7" fill="var(--teal)"/>
            <path d="M1 8 H15 M8 1 Q3 8 8 15 M8 1 Q13 8 8 15" stroke="var(--card)" stroke-width="1" fill="none"/>
          </svg>
          <span>www.quorvane.studio</span>
        </li>
      </ul>
    </div>

    <p class="email">avelkov@quorvane.studio</p>
  </section>

</main>
</body>
</html>
```